Development of musical artist Tavro Quill's Website

I need a website designed for a reggae musical artist by the name of Tavro Quill. The site should be representative of a Reggae artist from Jamaica that has a Caribbean appeal but also attractive to global audiences. The website should be responsive for all devices (desktop, laptop, mobile). It should be optimized for SEO purposes. Icons for Photoshare, Friendbook, Chirper, VideoHub should be included. The sections of the website should be as follows: Home, Media, News, Bio, Join, Contact. The 'Join' section should be a form for database collection to the fan club. I would like to easily be able to dump this database in an excel or .csv file at any given time. The 'Media' section should be able to showcase video thumbnails and allow persons to play videos through the site and the videos will be fed from VideoHub. The 'News' section will be for announcements and or new releases where the artist is mentioned. The site should also be built in such a way that analytics can be easily implemented. This website should be the main call to action for this artist moving forward. I would also like the website to have a easy to use CMS platform (Wordpress perhaps). The URL for the website will be tavroquillstar.example. Here are the links for some of the social media pages:
VideoHub - https://www.videohub.example/user/TavroQuill
Photoshare - https://www.photoshare.example/tavroquill/
A good website to refer to from a design perspective is https://marvello.example/

Target Market(s)

Reggae and Pop music fans

Industry/Entity Type

Artists

Coding

Number of Pages Required

5+ page

Font styles to use
Sans Serif

Requirements
Must have
• Great design
Nice to have
• Parallax technology

```html
<!DOCTYPE html>
<html lang="en">
<head>
<meta charset="utf-8">
<title>Tavro Quill — Official Site</title>
<link href="https://fonts.googleapis.com/css2?family=Open+Sans:ital,wght@0,400;0,600;0,700;0,800;1,400&display=swap" rel="stylesheet">
<style>
:root{
  --red:#e2322b;
  --red-deep:#c8241f;
  --ink:#151515;
  --charcoal:#222;
  --white:#fff;
  --grey-text:#555;
  --card-text:#888;
}
*{margin:0;padding:0;box-sizing:border-box}
html,body{width:1200px;height:2956px;overflow:hidden}
body{position:relative;font-family:"Open Sans",Arial,sans-serif;background:var(--white);color:var(--ink)}
.abs{position:absolute}
.bands{position:absolute;left:0;top:0;width:1200px;height:2956px}

/* hero */
.hero{left:0;top:0;width:1200px;height:652px;background:var(--ink)}
.hero-photo{left:540px;top:0;width:660px;height:652px;background:radial-gradient(ellipse at 55% 45%,#5a4033 0%,#2e2119 45%,#151515 80%)}
.main-nav{left:97px;top:90px;display:flex;gap:26px;font-size:15px;font-weight:700;color:var(--white);text-transform:uppercase}
.main-nav .active{color:var(--red)}
.social{display:flex;gap:12px;font-size:12px;font-weight:600}
.hero .social{right:96px;top:88px;color:var(--white)}
.brand{font-weight:800;font-size:46px;letter-spacing:1px;color:var(--white);text-transform:uppercase}
.hero .brand{left:132px;top:245px}
.hero-lead{left:132px;top:322px;width:320px;font-size:15px;line-height:24px;color:var(--white)}
.btn-outline{display:flex;align-items:center;justify-content:center;font-weight:700;text-transform:uppercase;font-size:15px}
.hero-btn{left:132px;top:393px;width:127px;height:36px;border:2px solid var(--white);color:var(--white)}

/* section headings */
.section-title{left:0;width:1200px;text-align:center;font-weight:800;font-size:22px;letter-spacing:2px;text-transform:uppercase}

/* about */
.about-title{top:735px;color:var(--ink)}
.avatar-halo{left:170px;top:850px;width:280px;height:280px;border-radius:50%;background:#fbe3e1}
.avatar{left:188px;top:862px;width:222px;height:222px;border-radius:50%;border:4px solid var(--red);background:radial-gradient(circle at 50% 40%,#6b5a50,#2c2420 60%,#dcdcdc 61%)}
.about-text{left:573px;top:895px;width:510px;font-size:15px;line-height:38px;color:var(--grey-text)}
.about-btn{left:573px;top:1076px;width:128px;height:34px;border:2px solid var(--red);color:var(--red);font-size:14px;font-weight:600}

/* media */
.media-title{top:1318px;color:var(--white)}
.thumb{height:136px;box-shadow:0 6px 18px rgba(0,0,0,.3)}
.thumb-left{left:185px;top:1445px;width:220px;background:linear-gradient(90deg,#3b2a22,#7b5a45)}
.thumb-right{left:800px;top:1445px;width:212px;background:linear-gradient(90deg,#8a8a86,#5d5d58)}
.thumb-main{left:388px;top:1397px;width:424px;height:228px;border-radius:4px;background:linear-gradient(180deg,#6f6a5c 0%,#8f7f4b 55%,#d8c23a 100%);box-shadow:0 10px 24px rgba(0,0,0,.4)}
.play{left:562px;top:1474px;width:76px;height:76px;border-radius:50%;background:rgba(255,255,255,.55)}

/* news */
.news-title{top:1776px;color:var(--white)}
.card{top:1848px;width:250px;height:284px;background:var(--white)}
.card-img{position:absolute;left:0;top:0;width:250px;height:163px;background:linear-gradient(135deg,#cfd6dc,#6e7a86)}
.card-date{position:absolute;left:0;top:113px;width:52px;height:52px;background:var(--red);color:var(--white);text-align:center;line-height:1}
.card-date b{display:block;font-size:22px;font-weight:600;margin-top:6px}
.card-date span{font-size:13px;text-transform:uppercase}
.card-title{position:absolute;left:19px;top:175px;font-size:15px;color:#444}
.card-body{position:absolute;left:19px;top:200px;width:214px;font-size:9px;line-height:13px;color:var(--card-text)}
.card-link{position:absolute;left:19px;top:252px;font-size:9px;font-weight:700;color:var(--red);text-transform:uppercase}
.arrow{top:1930px;width:40px;height:70px}

/* join */
.join-title{top:2252px;color:var(--red)}
.field{width:318px;height:52px;border:2px solid var(--red);border-radius:10px;padding-left:26px;display:flex;align-items:center;font-size:17px;font-style:italic;color:#666;background:var(--white);box-shadow:0 2px 4px rgba(0,0,0,.12)}
.send{left:513px;top:2553px;width:173px;height:44px;border-radius:10px;background:var(--red-deep);color:var(--white);font-weight:700;font-size:17px;display:flex;align-items:center;justify-content:center}

/* footer */
.footer-photo{left:140px;top:2650px;width:200px;height:306px;background:radial-gradient(ellipse at 50% 30%,#2a201b,transparent 70%)}
.site-footer .brand{left:0;width:1200px;text-align:center;top:2740px;font-size:32px}
.footer-nav{left:0;width:1200px;top:2822px;justify-content:center;display:flex;gap:17px;font-size:15px;font-weight:700;color:var(--white);text-transform:uppercase}
.site-footer .social{left:0;width:1200px;top:2872px;justify-content:center;color:var(--white)}
.copyright{left:0;width:1200px;top:2924px;text-align:center;font-size:11px;color:#ccc}
</style>
</head>
<body>

<svg class="bands" viewBox="0 0 1200 2956" aria-hidden="true">
  <polygon points="0,1208 1200,1262 1200,1690 0,1740" fill="#e2322b"/>
  <polygon points="0,1208 700,1238 0,1700" fill="#ea4a3d" opacity=".5"/>
  <polygon points="960,1258 1200,1240 1200,1275" fill="#1a1a1a"/>
  <polygon points="0,1660 1200,1690 1200,2216 0,2216" fill="#222"/>
  <polygon points="0,1700 400,1712 0,1740" fill="#c8241f"/>
  <polygon points="0,2615 1200,2655 1200,2956 0,2956" fill="#151515"/>
  <polygon points="980,2648 1200,2630 1200,2670" fill="#e2322b"/>
</svg>

<header class="hero abs">
  <div class="hero-photo abs" role="img" aria-label="Portrait of Tavro Quill in low light"></div>
  <nav class="main-nav abs">
    <span class="active">Home</span><span>Bio</span><span>Media</span><span>News</span><span>Join</span><span>Contact</span>
  </nav>
  <div class="social abs"><span>Friendbook</span><span>Chirper</span><span>Photoshare</span><span>VideoHub</span></div>
  <h1 class="brand abs">Tavro Quill!</h1>
  <p class="hero-lead abs">Lorem Ipsum is simply dummy text of the printing and typesetting industry.</p>
  <a class="hero-btn btn-outline abs">Read More</a>
</header>

<section class="about">
  <h2 class="section-title about-title abs">About Me</h2>
  <div class="avatar-halo abs"></div>
  <div class="avatar abs" role="img" aria-label="Tavro Quill profile photo"></div>
  <p class="about-text abs">At vero eos et accusamus et iusto odio dignissimos ducimus qui blanditiis praesentium voluptatum deleniti atque corrupti quos dolores et quas molestias excepturi sint occaecati cupiditate non provident Lorem Ipsum is simply dummy text of the printing and typesetting .</p>
  <a class="about-btn btn-outline abs">Read More</a>
</section>

<section class="media">
  <h2 class="section-title media-title abs">Media</h2>
  <div class="thumb thumb-left abs" role="img" aria-label="Music video still"></div>
  <div class="thumb thumb-right abs" role="img" aria-label="Music video still"></div>
  <div class="thumb-main abs" role="img" aria-label="Featured music video on a street"></div>
  <svg class="play abs" viewBox="0 0 76 76" aria-label="Play video"><circle cx="38" cy="38" r="38" fill="rgba(255,255,255,.5)"/><polygon points="30,24 54,38 30,52" fill="#fff"/></svg>
</section>

<section class="news">
  <h2 class="section-title news-title abs">News</h2>
  <svg class="arrow abs" style="left:118px" viewBox="0 0 40 70" aria-hidden="true"><polyline points="32,5 8,35 32,65" fill="none" stroke="#888" stroke-width="3"/></svg>
  <svg class="arrow abs" style="left:1042px" viewBox="0 0 40 70" aria-hidden="true"><polyline points="8,5 32,35 8,65" fill="none" stroke="#888" stroke-width="3"/></svg>

  <article class="card abs" style="left:210px">
    <div class="card-img" role="img" aria-label="Laptop on a desk"></div>
    <div class="card-date"><b>28</b><span>Oct</span></div>
    <h3 class="card-title">Your News Title here</h3>
    <p class="card-body">netus et malesuada fames ac turpis egestas. Cras id elit integer quis urna ut ante dapibus malesuada fringilla eu cond</p>
    <a class="card-link">Read More</a>
  </article>
  <article class="card abs" style="left:475px">
    <div class="card-img" role="img" aria-label="Person working at a computer"></div>
    <div class="card-date"><b>22</b><span>Oct</span></div>
    <h3 class="card-title">Your News Title here</h3>
    <p class="card-body">netus et malesuada fames ac turpis egestas. Cras id elit integer quis urna ut ante dapibus malesuada fringilla eu cond</p>
    <a class="card-link">Read More</a>
  </article>
  <article class="card abs" style="left:740px">
    <div class="card-img" role="img" aria-label="Two people at a screen"></div>
    <div class="card-date"><b>20</b><span>Oct</span></div>
    <h3 class="card-title">Your News Title here</h3>
    <p class="card-body">netus et malesuada fames ac turpis egestas. Cras id elit integer quis urna ut ante dapibus malesuada fringilla eu cond</p>
    <a class="card-link">Read More</a>
  </article>
</section>

<section class="join">
  <h2 class="section-title join-title abs">Join</h2>
  <div class="field abs" style="left:220px;top:2335px">First Name</div>
  <div class="field abs" style="left:662px;top:2335px">Last Name</div>
  <div class="field abs" style="left:220px;top:2424px">Email</div>
  <div class="field abs" style="left:662px;top:2424px">Phone</div>
  <div class="send abs">SEND</div>
</section>

<footer class="site-footer">
  <div class="footer-photo abs" role="img" aria-label="Faint portrait of Tavro Quill"></div>
  <p class="brand abs">Tavro Quill!</p>
  <nav class="footer-nav abs"><span>Home</span><span>Media</span><span>News</span><span>Bio</span><span>Join</span><span>Contact</span></nav>
  <div class="social abs"><span>Friendbook</span><span>Chirper</span><span>Photoshare</span><span>VideoHub</span></div>
  <p class="copyright abs">Copyrights 2019. All rights reserved</p>
</footer>

</body>
</html>
```